Tech business card design

We need an amazing business card design for our new business 'Pexla' a marketing tech startup based in Sydney, Australia. We provide an online marketplace for businesses to search and buy advertising media, connect with service providers and learn more about marketing. We wish to communicate 'cool tech', reliability and professionalism and design based around our logo.

Target Market(s)

Business Owners

Contact Information for Business Card

Name
Position
Email Address
Website
Phone Number

Font styles to use
Other font styles liked:
• Avenir & Avenir Next

Colors

Designer to choose colors to be used in the design.

```html
<!DOCTYPE html>
<html lang="en">
<head>
<meta charset="utf-8">
<title>Pexla business card</title>
<link rel="stylesheet" href="https://fonts.googleapis.com/css2?family=Exo+2:wght@700&family=Lato:wght@400;900&display=swap">
<style>
  :root {
    --backdrop: #80502a;
    --kraft-light: #dcbb92;
    --kraft-mid: #c9a074;
    --kraft-dark: #b7875a;
    --ink: #111111;
    --rule: #5a4630;
  }
  * { margin: 0; padding: 0; box-sizing: border-box; }
  html, body { width: 1200px; height: 900px; overflow: hidden; }
  body {
    position: relative;
    background: var(--backdrop);
    font-family: "Lato", sans-serif;
    color: var(--ink);
  }
  .card {
    position: absolute;
    width: 556px;
    height: 343px;
    background: linear-gradient(160deg, var(--kraft-light) 0%, var(--kraft-mid) 55%, var(--kraft-dark) 100%);
    box-shadow: 4px 5px 8px rgba(0, 0, 0, 0.45);
  }
  .card-front { left: 330px; top: 90px; }
  .card-back { left: 330px; top: 469px; width: 559px; }

  .holder { position: absolute; top: 96px; left: 0; right: 0; text-align: center; }
  .holder-name {
    font-family: "Exo 2", sans-serif;
    font-weight: 700;
    font-size: 22px;
    letter-spacing: 0.5px;
    line-height: 26px;
  }
  .holder-role { font-size: 16px; line-height: 20px; }

  .contact-divider {
    position: absolute;
    top: 155px;
    left: 188px;
    width: 179px;
    height: 24px;
    display: flex;
    align-items: center;
    justify-content: center;
    gap: 3px;
  }
  .contact-divider::before,
  .contact-divider::after {
    content: "";
    flex: 1;
    height: 1px;
    background: var(--rule);
  }
  .contact-icon { width: 21px; height: 21px; display: block; }

  .contact-list {
    position: absolute;
    top: 186px;
    left: 0;
    right: 0;
    list-style: none;
    text-align: center;
    font-size: 16px;
    line-height: 20.5px;
  }

  .brand-name {
    position: absolute;
    left: 0;
    right: 0;
    top: 118px;
    text-align: center;
    font-family: "Lato", sans-serif;
    font-weight: 900;
    font-size: 96px;
    letter-spacing: -1px;
    color: var(--ink);
  }
</style>
</head>
<body>
  <section class="card card-front" aria-label="Card front">
    <div class="holder">
      <h1 class="holder-name">DANIEL MARSH</h1>
      <p class="holder-role">Managing Director</p>
    </div>
    <div class="contact-divider">
      <svg class="contact-icon" viewBox="0 0 20 20" aria-label="Phone">
        <circle cx="10" cy="10" r="10" fill="#111"/>
        <path d="M5 8 Q10 4 15 8 L13.5 9.5 L12 8.5 L8 8.5 L6.5 9.5 Z M6.5 10.5 H13.5 V15 H6.5 Z" fill="#d2ab80"/>
        <circle cx="10" cy="12.7" r="1.2" fill="#111"/>
      </svg>
      <svg class="contact-icon" viewBox="0 0 20 20" aria-label="Email">
        <circle cx="10" cy="10" r="10" fill="#111"/>
        <rect x="4.5" y="6" width="11" height="8" fill="none" stroke="#d2ab80" stroke-width="1.3"/>
        <path d="M4.5 6 L10 10.5 L15.5 6" fill="none" stroke="#d2ab80" stroke-width="1.3"/>
      </svg>
      <svg class="contact-icon" viewBox="0 0 20 20" aria-label="Website">
        <circle cx="10" cy="10" r="10" fill="#111"/>
        <circle cx="10" cy="10" r="5.5" fill="none" stroke="#d2ab80" stroke-width="1.3"/>
        <path d="M7 7 Q9 9 8 12 M12 6 Q11 9 13 12" fill="none" stroke="#d2ab80" stroke-width="1.3"/>
      </svg>
    </div>
    <ul class="contact-list">
      <li>044-987 654 321</li>
      <li>hello@pexla.com</li>
      <li>www.pexlamedia.com</li>
    </ul>
  </section>

  <section class="card card-back" aria-label="Card back">
    <p class="brand-name">Pexla</p>
  </section>
</body>
</html>
```